Business Cards for a law firm

Business cards for our law firm. Use our silhoette logo and OAK PARTNERS - check our website (www.oakpartners.example)

Contact Information for Business Card

our silhouette logo, OAK PARTNERS, 800-555-0147, Dorian Pemberton, dorian@oakpartners.example

Requirements
Must have
• our silhouette logo, OAK PARTNERS, 800-555-0147, Dorian Pemberton, dorian@oakpartners.example

```html
<!DOCTYPE html>
<html lang="en">
<head>
<meta charset="utf-8">
<title>Oak Partners – Business Cards</title>
<link rel="stylesheet" href="https://fonts.googleapis.com/css2?family=Cinzel:wght@600;700&family=Arimo:wght@400;700&display=swap">
<style>
  :root {
    --navy: #1a2e68;
    --paper: #f4f4f5;
    --backdrop: #e3e3e3;
    --ink: #1d1d1f;
    --white: #ffffff;
  }
  * { margin: 0; padding: 0; box-sizing: border-box; }
  html, body {
    width: 1200px; height: 1040px; overflow: hidden;
    background: var(--backdrop);
  }
  .canvas { position: relative; width: 1200px; height: 1040px; }

  .card {
    position: absolute;
    width: 642px; height: 366px;
    border-radius: 16px;
  }
  .card--front { left: 285px; top: 130px; background: var(--paper); }
  .card--back  { left: 285px; top: 567px; background: var(--navy); }

  .brand {
    position: absolute; left: 328px; top: 46px;
    display: flex; align-items: center; gap: 12px;
  }
  .brand__mark {
    width: 34px; height: 34px; border-radius: 50%;
    background: var(--navy);
  }
  .brand__name {
    font-family: "Cinzel", serif; font-weight: 700;
    font-size: 21px; letter-spacing: 0.09em;
    color: var(--navy);
  }

  .person {
    position: absolute; left: 45px; top: 222px;
    font-family: "Cinzel", serif; font-weight: 700;
    font-size: 23px; letter-spacing: 0.02em;
    color: var(--navy);
  }
  .divider {
    position: absolute; left: 45px; top: 255px;
    width: 553px; height: 1px; background: var(--ink);
  }
  .contacts {
    position: absolute; left: 45px; top: 267px;
    list-style: none;
    font-family: "Arimo", sans-serif; font-size: 16px;
    color: var(--ink);
  }
  .contacts li {
    display: flex; align-items: center; gap: 8px;
    height: 20px;
  }
  .contacts svg { width: 12px; height: 12px; fill: var(--navy); flex: none; }

  .back-mark {
    position: absolute; left: 50%; top: 96px;
    transform: translateX(-50%);
    display: flex; flex-direction: column; align-items: center; gap: 22px;
  }
  .back-mark__circle {
    width: 120px; height: 120px; border-radius: 50%;
    background: var(--paper);
  }
  .back-mark__name {
    font-family: "Cinzel", serif; font-weight: 700;
    font-size: 26px; letter-spacing: 0.1em;
    color: var(--paper);
  }
  .back-url {
    position: absolute; left: 0; right: 0; top: 322px;
    text-align: center;
    font-family: "Arimo", sans-serif; font-weight: 700;
    font-size: 13px; letter-spacing: 0.34em;
    color: var(--paper);
  }
</style>
</head>
<body>
<main class="canvas">
  <section class="card card--front" aria-label="Business card front">
    <div class="brand">
      <span class="brand__mark"></span>
      <span class="brand__name">OAK PARTNERS</span>
    </div>
    <h1 class="person">Dorian Pemberton</h1>
    <div class="divider"></div>
    <ul class="contacts">
      <li>
        <svg viewBox="0 0 24 24" aria-hidden="true"><path d="M6.6 10.8a15.2 15.2 0 0 0 6.6 6.6l2.2-2.2c.3-.3.7-.4 1-.2 1.1.4 2.3.6 3.6.6.6 0 1 .4 1 1V20c0 .6-.4 1-1 1A17 17 0 0 1 3 4c0-.6.4-1 1-1h3.5c.6 0 1 .4 1 1 0 1.3.2 2.5.6 3.6.1.3 0 .7-.2 1z"/></svg>
        800-555-0147
      </li>
      <li>
        <svg viewBox="0 0 24 24" aria-hidden="true"><path d="M2 5h20v14H2zM4 7v.4l8 5.2 8-5.2V7zm0 2.8V17h16V9.8l-8 5.2z"/></svg>
        dorian@oakpartners.example
      </li>
      <li>
        <svg viewBox="0 0 24 24" aria-hidden="true"><circle cx="12" cy="12" r="10"/><path d="M8 6c2 1 3 2 2 4s-3 1-3 4 3 2 2 5M15 4c-1 2 1 3 3 3m-2 6c2 0 3 2 2 5" stroke="#f4f4f5" stroke-width="1.6" fill="none"/></svg>
        www.oakpartners.example
      </li>
    </ul>
  </section>

  <section class="card card--back" aria-label="Business card back">
    <div class="back-mark">
      <span class="back-mark__circle"></span>
      <span class="back-mark__name">OAK PARTNERS</span>
    </div>
    <p class="back-url">WWW.OAKPARTNERS.EXAMPLE</p>
  </section>
</main>
</body>
</html>
```